Building company buisness cards

We are looking for a sharp modern new look for our business cards.
We are a New Zealand based company that specialises in house and land packages.
We have attached a photo of the current logo and would like to see if it can be improved somehow if needed.
We are open to any colours but we have chosen green at this stage.
Feel free to change the font and make the logo smarter looking.
Play with the colours and see what looks best.

We want a card that looks so good know one will want to throw it away!

Target Market(s)

Home buyers

Industry/Entity Type

Building

Contact Information for Business Card

Derek Tolvane
0217394062
dtolvane@quillmarkhomesteads.co.nz
quillmarkhomesteads.co.nz

Font styles to use
Serif
Sans Serif

Colors

Designer to choose colors to be used in the design.

Requirements
Must have
• Logo and company name on one side, details on the other side
Nice to have
• Color codes for the original green are HEX #4a8028, RGB(74,128,40), CMYK(42,0,69,50)
• Round corners, Raised and/or spot UV

```html
<!DOCTYPE html>
<html lang="en">
<head>
<meta charset="utf-8">
<title>Quillmark Homesteads – Business Cards</title>
<link rel="stylesheet" href="https://fonts.googleapis.com/css2?family=Montserrat:wght@600;800&family=Roboto:wght@400&display=swap">
<style>
  :root {
    --brand-green: #4a8028;
    --stripe-grey: #6f6f6f;
    --card-white: #ffffff;
    --backdrop: #2b2d2f;
    --text-light: #ffffff;
  }
  * { margin: 0; padding: 0; box-sizing: border-box; }
  html, body {
    width: 1200px;
    height: 738px;
    overflow: hidden;
    background: var(--backdrop);
  }
  .canvas {
    position: relative;
    width: 1200px;
    height: 738px;
    display: flex;
    align-items: center;
    justify-content: center;
    gap: 40px;
  }
  .card {
    position: relative;
    width: 540px;
    height: 309px;
    border-radius: 6px;
    overflow: hidden;
  }

  /* Front side */
  .card--front {
    background: var(--brand-green);
    color: var(--text-light);
  }
  .front-wordmark {
    position: absolute;
    top: 92px;
    left: 0;
    right: 0;
    text-align: center;
    font-family: "Montserrat", sans-serif;
    font-weight: 800;
    font-size: 38px;
    line-height: 1.02;
    letter-spacing: -0.5px;
    text-transform: lowercase;
  }
  .front-web {
    position: absolute;
    bottom: 26px;
    left: 0;
    right: 0;
    text-align: center;
    font-family: "Roboto", sans-serif;
    font-size: 12px;
    letter-spacing: 0.6px;
  }

  /* Back side */
  .card--back { background: var(--card-white); }
  .back-wave {
    position: absolute;
    inset: 0;
    width: 100%;
    height: 100%;
  }
  .back-wordmark {
    position: absolute;
    top: 78px;
    left: 30px;
    font-family: "Montserrat", sans-serif;
    font-weight: 800;
    font-size: 27px;
    line-height: 1.02;
    letter-spacing: -0.4px;
    color: var(--brand-green);
    text-transform: lowercase;
  }
  .holder {
    position: absolute;
    top: 168px;
    right: 26px;
    text-align: right;
    color: var(--text-light);
  }
  .holder-name {
    font-family: "Montserrat", sans-serif;
    font-weight: 600;
    font-size: 22px;
    line-height: 1;
  }
  .holder-role {
    font-family: "Roboto", sans-serif;
    font-size: 11px;
    margin-top: 2px;
  }
  .contact-list {
    position: absolute;
    top: 224px;
    right: 20px;
    list-style: none;
    text-align: right;
    font-family: "Roboto", sans-serif;
    font-size: 12px;
    line-height: 16px;
    color: var(--text-light);
  }
  .contact-list li {
    display: flex;
    justify-content: flex-end;
    align-items: center;
    gap: 6px;
  }
  .contact-icon {
    width: 9px;
    height: 9px;
    flex: none;
  }
</style>
</head>
<body>
<main class="canvas">

  <section class="card card--front" aria-label="Business card front">
    <div class="front-wordmark">quillmark<br>homesteads.</div>
    <div class="front-web">www.quillmarkhomesteads.co.nz</div>
  </section>

  <section class="card card--back" aria-label="Business card back">
    <svg class="back-wave" viewBox="0 0 540 309" preserveAspectRatio="none" aria-hidden="true">
      <path fill="var(--stripe-grey)" d="M0,236 C140,290 240,220 320,150 C400,90 470,82 540,86 L540,309 L0,309 Z"/>
      <path fill="var(--card-white)" d="M0,243 C140,297 240,227 320,157 C400,97 470,89 540,93 L540,309 L0,309 Z"/>
      <path fill="var(--brand-green)" d="M0,247 C140,301 240,231 320,161 C400,101 470,93 540,97 L540,309 L0,309 Z"/>
    </svg>

    <div class="back-wordmark">quillmark<br>homesteads.</div>

    <div class="holder">
      <div class="holder-name">Derek Tolvane</div>
      <div class="holder-role">Founder</div>
    </div>

    <ul class="contact-list">
      <li>0217394062
        <svg class="contact-icon" viewBox="0 0 10 10" aria-hidden="true"><path fill="none" stroke="#fff" stroke-width="1.2" d="M2,1 L4,3 L3,4 C4,6 5,7 6,7 L7,6 L9,8 L8,9 C4,9 1,6 1,2 Z"/></svg>
      </li>
      <li>dtolvane@quillmarkhomesteads.co.nz
        <svg class="contact-icon" viewBox="0 0 10 10" aria-hidden="true"><rect x="0.6" y="2" width="8.8" height="6" fill="none" stroke="#fff" stroke-width="1"/><path d="M0.6,2 L5,5.5 L9.4,2" fill="none" stroke="#fff" stroke-width="1"/></svg>
      </li>
      <li>www.quillmarkhomesteads.co.nz
        <svg class="contact-icon" viewBox="0 0 10 10" aria-hidden="true"><circle cx="5" cy="5" r="4.2" fill="none" stroke="#fff" stroke-width="1"/><ellipse cx="5" cy="5" rx="1.8" ry="4.2" fill="none" stroke="#fff" stroke-width="0.8"/><line x1="0.8" y1="5" x2="9.2" y2="5" stroke="#fff" stroke-width="0.8"/></svg>
      </li>
    </ul>
  </section>

</main>
</body>
</html>
```